Lucky Harbour Fun Casino Entertainment

Looking to update my business card and make it look more modern, stand out and eye catching.
We are are fun casino business in Australia (primarily Sydney). Blackjack and Roulette are our most popular games although we have pretty much every game available for hire that you would find in a real casino. The final design would need to be sleek and appeal to the more upmarket corporate sector.
We mainly cater for Corporate Events, Private Parties, Fundraising Events, Team Building, Poker Tournaments
I think I'd prefer the colour Black.

Target Market(s)

High-end Corporate

Industry/Entity Type

Events

Contact Information for Business Card

Rob Kendall
Director
1300 482 617
0433 728 591
info@luckyharbour.com.au
www.luckyharbour.com.au
Facebook & Instagram @luckyharbourevents (proper social icons preferred)

Colors
000000
0255a3

Requirements
Must have
• Front side:
• Logo
• Contact details
• 'Australia's #1 Fun Casino Specialists'
• Back:
• Logo
Nice to have
• Back:
• Corporate Events
• Private Parties
• Poker Tournaments
• Fundraising
• Props & Theming
• Photo Booth
• Horse Racing Events
• The Vegas Sign attached, maybe on the back of the card in the background...?

```html
<!DOCTYPE html>
<html lang="en">
<head>
<meta charset="utf-8">
<title>Lucky Harbour Fun Casino Entertainment – Business Card</title>
<link rel="stylesheet" href="https://fonts.googleapis.com/css2?family=Montserrat:wght@400;500;600;700&display=swap">
<style>
  :root {
    --stage: #2a2b2e;
    --card: #1d1e21;
    --card-edge: #2c2d31;
    --gold: #f7b500;
    --gold-light: #ffd21a;
    --white: #f2f2f2;
    --ink: #111111;
    --chip-blue: #0255a3;
    --chip-blue-light: #3a7fd0;
  }
  * { box-sizing: border-box; margin: 0; padding: 0; }
  html, body {
    width: 1200px; height: 800px; overflow: hidden;
    background: var(--stage);
    font-family: "Montserrat", sans-serif;
  }
  .canvas {
    position: relative; width: 1200px; height: 800px;
    display: flex; align-items: center; justify-content: center; gap: 40px;
  }
  .card {
    position: relative; width: 540px; height: 310px;
    background: var(--card);
    border-radius: 14px;
    border: 1px solid var(--card-edge);
    box-shadow: 0 18px 40px rgba(0,0,0,.45);
    overflow: hidden;
  }
  /* brand mark */
  .brand {
    position: absolute; display: flex; align-items: center; gap: 12px;
  }
  .brand__dot {
    width: 30px; height: 30px; border-radius: 50%; background: var(--gold); flex: none;
  }
  .brand__name {
    font-weight: 700; font-size: 26px; line-height: 1.05; color: var(--gold);
    text-transform: uppercase; letter-spacing: .5px;
  }
  .divider {
    position: absolute; width: 1px;
    background: linear-gradient(to bottom, transparent, var(--gold) 30%, var(--gold) 70%, transparent);
  }
  /* front */
  .card--front .brand { left: 34px; top: 92px; }
  .card--front .divider { left: 262px; top: 40px; height: 150px; }
  .contact { position: absolute; left: 290px; top: 30px; color: var(--white); }
  .contact__name { color: var(--gold); font-weight: 600; font-size: 17px; text-transform: uppercase; }
  .contact__role { font-size: 12.5px; margin-bottom: 10px; }
  .contact__list { list-style: none; }
  .contact__item { display: flex; align-items: center; gap: 8px; font-size: 12px; height: 19px; }
  .icon { width: 14px; height: 14px; flex: none; }
  .contact__social { display: flex; align-items: center; gap: 6px; margin-top: 8px; font-size: 12px; }
  .social-dot { width: 14px; height: 14px; border-radius: 50%; background: var(--gold); }
  .tagline-band {
    position: absolute; left: 0; right: 0; bottom: 30px; height: 40px;
    background: linear-gradient(to right, var(--gold), var(--gold-light));
    display: flex; align-items: center; justify-content: center;
    color: var(--ink); font-weight: 600; font-size: 15px; letter-spacing: 1.5px;
  }
  /* back */
  .card--back .brand { left: 60px; top: 128px; }
  .card--back .divider { left: 300px; top: 70px; height: 170px; }
  .services { position: absolute; left: 326px; top: 72px; list-style: none; color: var(--white); }
  .services__item { display: flex; align-items: center; gap: 10px; font-size: 13px; height: 24px; }
  .chip {
    width: 13px; height: 13px; border-radius: 50%; flex: none;
    background: var(--chip-blue);
    border: 2px dashed #ffffff;
  }
</style>
</head>
<body>
<main class="canvas">

  <section class="card card--front" aria-label="Business card front">
    <div class="brand">
      <span class="brand__dot"></span>
      <span class="brand__name">Lucky<br>Harbour</span>
    </div>
    <span class="divider"></span>
    <div class="contact">
      <p class="contact__name">Rob Kendall</p>
      <p class="contact__role">Director</p>
      <ul class="contact__list">
        <li class="contact__item">
          <svg class="icon" viewBox="0 0 14 14"><circle cx="7" cy="7" r="7" fill="var(--gold)"/><path d="M4.5 3.5l1.6 0 .6 1.8-1 .7a5 5 0 0 0 2.3 2.3l.7-1 1.8.6v1.6c0 .4-.4.8-.8.8A6 6 0 0 1 3.7 4.3c0-.4.4-.8.8-.8z" fill="var(--ink)"/></svg>
          1300 482 617
        </li>
        <li class="contact__item">
          <svg class="icon" viewBox="0 0 14 14"><circle cx="7" cy="7" r="7" fill="var(--gold)"/><rect x="4.8" y="3" width="4.4" height="8" rx="1" fill="none" stroke="var(--ink)" stroke-width="1.2"/></svg>
          0433 728 591
        </li>
        <li class="contact__item">
          <svg class="icon" viewBox="0 0 14 14"><circle cx="7" cy="7" r="7" fill="var(--gold)"/><rect x="3.5" y="4.5" width="7" height="5" fill="none" stroke="var(--ink)" stroke-width="1.1"/><path d="M3.5 4.5L7 7.5l3.5-3" fill="none" stroke="var(--ink)" stroke-width="1.1"/></svg>
          info@luckyharbour.com.au
        </li>
        <li class="contact__item">
          <svg class="icon" viewBox="0 0 14 14"><circle cx="7" cy="7" r="7" fill="var(--gold)"/><circle cx="7" cy="7" r="3.6" fill="none" stroke="var(--ink)" stroke-width="1.1"/><path d="M3.4 7h7.2M7 3.4c-1.6 2-1.6 5.2 0 7.2M7 3.4c1.6 2 1.6 5.2 0 7.2" fill="none" stroke="var(--ink)" stroke-width=".9"/></svg>
          www.luckyharbour.com.au
        </li>
      </ul>
      <p class="contact__social"><span class="social-dot"></span><span class="social-dot"></span>@luckyharbourevents</p>
    </div>
    <div class="tagline-band">Australia's #1 Fun Casino Specialists</div>
  </section>

  <section class="card card--back" aria-label="Business card back">
    <div class="brand">
      <span class="brand__dot"></span>
      <span class="brand__name">Lucky<br>Harbour</span>
    </div>
    <span class="divider"></span>
    <ul class="services">
      <li class="services__item"><span class="chip"></span>Corporate Events</li>
      <li class="services__item"><span class="chip"></span>Private Parties</li>
      <li class="services__item"><span class="chip"></span>Poker Tournaments</li>
      <li class="services__item"><span class="chip"></span>Fundraising</li>
      <li class="services__item"><span class="chip"></span>Props &amp; Theming</li>
      <li class="services__item"><span class="chip"></span>Photo Booth</li>
      <li class="services__item"><span class="chip"></span>Horse Racing Events</li>
    </ul>
  </section>

</main>
</body>
</html>
```